Frostvale Harborline LLC

we need a business card design

Industry/Entity Type

hvac

Contact Information for Business Card

my logo

Requirements
Must have
• my logo and same colors

```html
<!DOCTYPE html>
<html lang="en">
<head>
<meta charset="utf-8">
<title>Frostvale Harborline LLC – Business Card</title>
<link rel="stylesheet" href="https://fonts.googleapis.com/css2?family=Montserrat:wght@400;500;700&display=swap">
<style>
  :root {
    --page: #3a3a3c;
    --brand-blue: #0f5ea8;
    --sky: #22aae2;
    --gold: #f5b94a;
    --white: #ffffff;
  }
  * { margin: 0; padding: 0; box-sizing: border-box; }
  html, body { width: 1200px; height: 875px; overflow: hidden; }
  body {
    background: var(--page);
    font-family: "Montserrat", sans-serif;
    position: relative;
  }
  .card {
    position: absolute;
    width: 560px;
    height: 320px;
    border-radius: 18px;
    overflow: hidden;
    background: var(--brand-blue);
    box-shadow: 0 14px 30px rgba(0,0,0,.35);
  }
  .card--front { left: 60px; top: 100px; }
  .card--back  { left: 580px; top: 455px; }

  .brand-lockup {
    position: absolute;
    inset: 0;
    display: flex;
    align-items: center;
    justify-content: center;
    gap: 14px;
  }
  .brand-lockup__dot {
    width: 22px; height: 22px; border-radius: 50%;
    background: var(--gold);
    flex: none;
  }
  .brand-lockup__name {
    font-weight: 700;
    color: var(--white);
    font-size: 30px;
    line-height: 1.1;
    letter-spacing: .5px;
  }
  .card--back .brand-lockup {
    left: 330px; right: 0; top: 0; bottom: 90px;
    flex-direction: column;
    gap: 10px;
    text-align: center;
  }
  .card--back .brand-lockup__name {
    color: var(--brand-blue);
    font-size: 20px;
  }

  .back-swoosh { position: absolute; inset: 0; }

  .contact {
    position: absolute;
    left: 40px; top: 60px;
    width: 290px;
    color: var(--white);
  }
  .contact__name {
    font-weight: 700;
    font-size: 24px;
    color: var(--sky);
    text-transform: uppercase;
    letter-spacing: .5px;
  }
  .contact__role { font-size: 13px; margin-top: 2px; }
  .contact__rule {
    height: 1px;
    background: var(--gold);
    margin: 12px 0;
    width: 250px;
  }
  .contact__address { font-size: 13px; line-height: 1.45; }
  .contact__list { list-style: none; font-size: 13px; line-height: 1.9; }
  .contact__list li { display: flex; align-items: center; gap: 9px; }
  .contact__icon { width: 12px; height: 12px; flex: none; }
</style>
</head>
<body>

  <section class="card card--front" aria-label="Card front">
    <div class="brand-lockup">
      <span class="brand-lockup__dot"></span>
      <span class="brand-lockup__name">Frostvale Harborline LLC</span>
    </div>
  </section>

  <section class="card card--back" aria-label="Card back">
    <svg class="back-swoosh" viewBox="0 0 560 320" preserveAspectRatio="none" aria-hidden="true">
      <path d="M318 0 Q290 250 560 335 L560 0 Z" fill="#22aae2"/>
      <path d="M326 0 Q302 238 560 322 L560 0 Z" fill="#f5b94a"/>
      <path d="M334 0 Q314 228 560 308 L560 0 Z" fill="#ffffff"/>
    </svg>

    <div class="brand-lockup">
      <span class="brand-lockup__dot"></span>
      <span class="brand-lockup__name">Frostvale Harborline LLC</span>
    </div>

    <div class="contact">
      <h1 class="contact__name">Dana Whitlock</h1>
      <p class="contact__role">Founder</p>
      <div class="contact__rule"></div>
      <p class="contact__address">24 Kestrel Bend Rd<br>Marlow Flats ABC 4410</p>
      <div class="contact__rule"></div>
      <ul class="contact__list">
        <li>
          <svg class="contact__icon" viewBox="0 0 12 12"><path d="M2.5 1 L4.5 1 L5.3 3.4 L4 4.4 Q5 6.8 7.6 8 L8.6 6.7 L11 7.5 L11 9.5 Q10.5 11 9 11 Q1 10 1 2.5 Q1 1 2.5 1Z" fill="#f5b94a"/></svg>
          555.214.0387
        </li>
        <li>
          <svg class="contact__icon" viewBox="0 0 12 12"><rect x="0.5" y="2" width="11" height="8" fill="#f5b94a"/><path d="M0.5 2 L6 6.5 L11.5 2" fill="none" stroke="#0f5ea8" stroke-width="1"/></svg>
          info@frostvaleharbor.com
        </li>
        <li>
          <svg class="contact__icon" viewBox="0 0 12 12"><circle cx="6" cy="6" r="5.2" fill="none" stroke="#f5b94a" stroke-width="1.2"/><ellipse cx="6" cy="6" rx="2.2" ry="5.2" fill="none" stroke="#f5b94a" stroke-width="1"/><line x1="0.8" y1="6" x2="11.2" y2="6" stroke="#f5b94a" stroke-width="1"/></svg>
          www.frostvaleharbor.com
        </li>
      </ul>
    </div>
  </section>

</body>
</html>
```